Wattle Kitchen logo

I am a catering and food business that requires a logo for my website and all related business branding. I also need a label for my hot sauce. You can find my information on Facebook and there is a picture of the logo I currently use and also a bottle of my hot sauce.
I am based in the Adelaide Hills in South Australia. I would like to use black and gold or Purple and gold my colour scheme and really like the hornet cartoon that I currently use. Something more refined and original would be great...
Catering

```html
<!DOCTYPE html>
<html lang="en">
<head>
<meta charset="utf-8">
<title>Ember Sauce – Label</title>
<link rel="stylesheet" href="https://fonts.googleapis.com/css2?family=Barlow+Condensed:wght@400;500;600&family=Russo+One&family=Oswald:wght@300;400&display=swap">
<style>
  :root {
    --canvas: #ffffff;
    --paper: #e4e4e2;
    --paper-light: #efefed;
    --ink: #141414;
    --white: #f4f4f2;
    --red: #b3262a;
    --gold: #c9a43a;
  }
  * { margin: 0; padding: 0; box-sizing: border-box; }
  html, body { width: 1200px; height: 1000px; overflow: hidden; background: var(--canvas); }
  .canvas { position: relative; width: 1200px; height: 1000px; }
  .label {
    position: absolute; left: 300px; top: 200px; width: 600px; height: 600px;
    background: radial-gradient(circle at 40% 30%, var(--paper-light), var(--paper));
    font-family: "Barlow Condensed", sans-serif; color: var(--white); overflow: hidden;
  }
  .label-band { position: absolute; inset: 0; width: 600px; height: 600px; }
  .brand-mark {
    position: absolute; display: flex; flex-direction: column; align-items: center; justify-content: center;
    border: 1.5px solid var(--ink); border-radius: 50%;
  }
  .brand-mark span { font-family: "Barlow Condensed", sans-serif; font-weight: 600; color: var(--ink); text-transform: uppercase; text-align: center; line-height: 1.05; }
  .brand-mark--top { left: 114px; top: 28px; width: 74px; height: 74px; }
  .brand-mark--top span { font-size: 13px; }
  .brand-mark--foot { top: 542px; width: 42px; height: 42px; }
  .brand-mark--foot span { font-size: 7.5px; }
  .brand-mark--left { left: 24px; }
  .brand-mark--right { left: 536px; }
  .kicker { position: absolute; left: 45px; top: 217px; font-family: "Oswald", sans-serif; font-weight: 400; font-size: 15px; letter-spacing: 2.6px; color: var(--red); }
  .product-name { position: absolute; left: 43px; top: 240px; font-family: "Russo One", sans-serif; font-size: 44px; line-height: 46px; letter-spacing: 2px; color: var(--white); }
  .rule { position: absolute; left: 45px; width: 218px; height: 1px; background: var(--gold); }
  .rule--top { top: 337px; } .rule--bottom { top: 381px; }
  .uses { position: absolute; left: 45px; top: 340px; width: 218px; font-weight: 500; color: var(--red); text-transform: uppercase; line-height: 18px; }
  .uses .line1 { font-size: 14.5px; letter-spacing: 0.2px; }
  .uses .line2 { font-size: 17px; font-weight: 600; }
  .volume { position: absolute; left: 45px; width: 220px; top: 418px; text-align: center; font-size: 17px; }
  .origin { position: absolute; left: 45px; width: 220px; top: 441px; text-align: center; font-size: 13px; color: var(--red); letter-spacing: 0.3px; }

  .nutrition { position: absolute; left: 373px; top: 216px; width: 179px; height: 178px; border: 1px solid var(--gold); font-size: 11px; line-height: 12px; }
  .nutrition h2 { font-family: "Oswald", sans-serif; font-weight: 400; font-size: 13px; line-height: 15px; letter-spacing: 1px; text-align: center; margin: 2px 0 1px; }
  .nutrition table { width: 100%; border-collapse: collapse; table-layout: fixed; }
  .nutrition col.c-name { width: 73px; }
  .nutrition col.c-serve { width: 56px; }
  .nutrition td { padding: 0 0 0 4px; vertical-align: top; white-space: nowrap; overflow: hidden; }
  .nutrition .sep td { border-top: 1px solid var(--gold); }
  .nutrition .head td { padding-top: 9px; padding-bottom: 6px; }
  .nutrition .body-first td { padding-top: 4px; }
  .nutrition .indent { padding-left: 9px; }

  .ingredients { position: absolute; left: 377px; top: 404px; width: 182px; font-size: 10.5px; line-height: 13px; text-transform: uppercase; }
  .address { position: absolute; left: 72px; top: 556px; font-size: 13px; font-weight: 600; color: var(--ink); text-transform: uppercase; letter-spacing: 0.2px; }
</style>
</head>
<body>
<main class="canvas">
  <section class="label">
    <svg class="label-band" viewBox="0 0 600 600" aria-hidden="true">
      <defs>
        <radialGradient id="bandShade" cx="45%" cy="45%" r="70%">
          <stop offset="0" stop-color="#262626"/>
          <stop offset="1" stop-color="#121212"/>
        </radialGradient>
      </defs>
      <polygon fill="url(#bandShade)" points="0,150 18,140 34,146 52,132 70,138 92,127 110,134 132,124 150,131 172,121 196,128 214,119 236,126 258,118 280,127 300,120 322,129 344,121 366,131 388,124 410,135 430,127 452,137 474,128 496,139 518,131 540,142 562,134 584,144 600,138
        600,515 580,509 558,518 536,507 514,514 492,505 470,512 448,503 426,510 404,502 380,512 358,505 336,516 312,508 290,519 268,510 246,520 224,512 200,522 178,514 156,524 134,516 112,525 90,517 68,527 46,519 24,528 0,522"/>
    </svg>

    <div class="brand-mark brand-mark--top"><span>Wattle<br>Kitchen</span></div>

    <p class="kicker">AUSTRALIAN HOT SAUCE</p>
    <h1 class="product-name">EMBER<br>SAUCE</h1>
    <div class="rule rule--top"></div>
    <p class="uses"><span class="line1">Hot sauce, marinade, condiment</span><br><span class="line2">&amp; extreme flavour bringer</span></p>
    <div class="rule rule--bottom"></div>
    <p class="volume">250 ML</p>
    <p class="origin">PRODUCT OF AUSTRALIA</p>

    <div class="nutrition">
      <h2>NUTRITION FACTS</h2>
      <table>
        <colgroup><col class="c-name"><col class="c-serve"><col class="c-100"></colgroup>
        <tr><td colspan="2">servings per package:</td><td>25.00</td></tr>
        <tr><td colspan="2">serving size:</td><td>10.00ml</td></tr>
        <tr class="sep head"><td></td><td>avg. qty.<br>per serving</td><td>avg. qty.<br>per 100ml</td></tr>
        <tr class="sep body-first"><td>energy</td><td>85 kJ</td><td>848 kJ</td></tr>
        <tr><td>protein</td><td>0.1 g</td><td>1.3 g</td></tr>
        <tr><td>fat, total</td><td>1.1 g</td><td>11.1 g</td></tr>
        <tr><td class="indent">saturated</td><td>0.2 g</td><td>1.6 g</td></tr>
        <tr><td>carbohydrate</td><td>2.3 g</td><td>23.2 g</td></tr>
        <tr><td class="indent">sugars</td><td>2.2 g</td><td>21.7 g</td></tr>
        <tr><td>sodium</td><td>41 mg</td><td>412 mg</td></tr>
      </table>
    </div>
    <p class="ingredients">Ingredients: capsicum, water, vinegar, sugar, garlic, lemon juice, olive oil, chilli, spices, cornstarch, almond, salt.</p>

    <div class="brand-mark brand-mark--foot brand-mark--left"><span>Wattle<br>Kitchen</span></div>
    <p class="address">48 Ridge Lane. Stirling Heights, S.A. 5999</p>
    <div class="brand-mark brand-mark--foot brand-mark--right"><span>Wattle<br>Kitchen</span></div>
  </section>
</main>
</body>
</html>
```